Valdane Companies Business Card Design

We need a new business card for our Private Equity Real Estate Development firm, “Valdane” and our EB-5 regional center “Thornmere Regional Center” on one card. We prefer a design that is simple, elegant, and represents the luxury products we design and build as well as the financial security and stability our successful history has produced. We are an industry leader in our field and 3rd generation family business that has evolved into an institutional quality investment platform. Considered design size is standard business card dimensions (3.5 x 2 inches with an additional 1/8 inch space for design elements or backgrounds that extend beyond the finished size of your piece.

Target Market(s)

• High net worth individuals
• Highly skilled technical workers and physicians in the US seeking investment-based immigration opportunities
• Sophisticated private equity investors
• Intermediary partners include domestic attorneys and investment brokers, as well as international agent networks
• US real estate developers

Industry/Entity Type

Finance

Contact Information for Business Card

(Providing placeholder info for personal information, please design for longer character spaces, longer names and addresses etc..)
• Logo for Valdane
• Logo for Thornmere Regional Center
• Full name: Marcus Valdane
• Job title: CEO
• Email address: mvaldane@valdanecompanies.com
• Cell phone number: +1.555.314.2287
• Office number +1.555.628.4410
• Office address: Larkfield Court 5, 4817 Vista Orilla, Ashvale, NV.
• Website: www.valdanecompanies.com

Font styles to use
Serif
Sans Serif

Colors
ec1f27
ffffff
000000

Requirements
Must have
• • Logo for Valdane
• • Logo for Thornmere Regional Center
• - Use rounded corners
• (See .ai file included for logos)
Nice to have
• • Simple, elegant design
• • Aesthetically compatible with our website design (www.valdanecompanies.com)
• • Color palette including but not limited to white, black, and red (as per logos)
Should not have
• - Not too much red color
• - Do not stack both logos on top of each other

```html
<!DOCTYPE html>
<html lang="en">
<head>
<meta charset="utf-8">
<title>Valdane Companies Business Card</title>
<link rel="stylesheet" href="https://fonts.googleapis.com/css2?family=Cinzel:wght@400;700&family=Open+Sans:wght@400;600&display=swap">
<style>
  :root {
    --red: #a51c30;
    --white: #ffffff;
    --black: #1c1c1e;
    --ink: #111111;
    --rule: #b5b5b5;
    --stage: #2a2a2c;
    --pattern: #27272a;
  }
  * { box-sizing: border-box; margin: 0; padding: 0; }
  html, body { width: 1200px; height: 1108px; overflow: hidden; }
  body {
    background: var(--stage);
    display: flex;
    align-items: center;
    justify-content: center;
    gap: 80px;
    font-family: "Open Sans", sans-serif;
  }
  .card {
    position: relative;
    width: 400px;
    height: 700px;
    border-radius: 30px;
    overflow: hidden;
  }
  .card-front { background: var(--white); color: var(--ink); }
  .card-back { background: var(--black); }

  .brand {
    position: absolute;
    top: 150px;
    left: 0; right: 0;
    display: flex;
    align-items: center;
    justify-content: center;
    gap: 16px;
  }
  .brand-mark { width: 54px; height: 54px; background: var(--ink); }
  .brand-name {
    font-family: "Cinzel", serif;
    font-weight: 700;
    font-size: 44px;
    letter-spacing: 1px;
    color: var(--ink);
  }

  .person { position: absolute; top: 300px; left: 0; right: 0; text-align: center; z-index: 2; }
  .person-name {
    font-family: "Cinzel", serif;
    font-weight: 400;
    font-size: 27px;
    color: var(--red);
    letter-spacing: 0.5px;
  }
  .person-title { font-size: 15px; margin-top: 2px; }

  .divider {
    display: flex;
    align-items: center;
    gap: 6px;
    margin: 8px 44px;
  }
  .divider::before, .divider::after {
    content: ""; flex: 1; height: 1px; background: var(--rule);
  }
  .icon {
    width: 20px; height: 20px;
    border-radius: 4px;
    background: var(--red);
    display: flex; align-items: center; justify-content: center;
  }
  .icon svg { width: 12px; height: 12px; }

  .contact { text-align: center; font-size: 16px; line-height: 22px; }
  .address { text-align: center; font-size: 16px; line-height: 22px; }

  .footer-band { position: absolute; left: 0; bottom: 0; width: 400px; height: 120px; z-index: 1; }

  .pattern-field { position: absolute; inset: 0; background: linear-gradient(160deg, var(--pattern), var(--black)); }
  .center-brand {
    position: absolute;
    left: 40px; right: 30px; bottom: 70px;
    display: flex; align-items: center; gap: 16px;
  }
  .center-mark { width: 60px; height: 60px; background: var(--white); flex: none; }
  .center-text { border-left: 1px solid var(--white); padding-left: 14px; color: var(--white); }
  .center-name {
    font-family: "Cinzel", serif;
    font-weight: 700;
    font-size: 30px;
    line-height: 1;
  }
  .center-sub {
    font-family: "Cinzel", serif;
    font-weight: 700;
    font-size: 11px;
    letter-spacing: 5px;
    margin-top: 6px;
  }
</style>
</head>
<body>
  <section class="card card-front">
    <div class="brand">
      <div class="brand-mark"></div>
      <div class="brand-name">VALDANE</div>
    </div>

    <div class="person">
      <h1 class="person-name">MARCUS VALDANE</h1>
      <p class="person-title">CEO</p>

      <div class="divider">
        <span class="icon"><svg viewBox="0 0 12 12"><path d="M2 1h3l1 3-2 1a7 7 0 0 0 3 3l1-2 3 1v3c-6 0-9-3-9-9z" fill="#fff"/></svg></span>
        <span class="icon"><svg viewBox="0 0 12 12"><rect x="3" y="0.5" width="6" height="11" rx="1" fill="none" stroke="#fff" stroke-width="1.3"/></svg></span>
        <span class="icon"><svg viewBox="0 0 12 12"><rect x="1" y="2.5" width="10" height="7" fill="none" stroke="#fff" stroke-width="1.2"/><path d="M1 3l5 4 5-4" fill="none" stroke="#fff" stroke-width="1.2"/></svg></span>
        <span class="icon"><svg viewBox="0 0 12 12"><circle cx="6" cy="6" r="5" fill="none" stroke="#fff" stroke-width="1.2"/><path d="M1 6h10M6 1c-3 3-3 7 0 10M6 1c3 3 3 7 0 10" fill="none" stroke="#fff" stroke-width="1"/></svg></span>
      </div>

      <div class="contact">
        <p>+1.555.314.2287</p>
        <p>+1.555.628.4410</p>
        <p>mvaldane@valdanecompanies.com</p>
        <p>www.valdanecompanies.com</p>
      </div>

      <div class="divider">
        <span class="icon"><svg viewBox="0 0 12 12"><path d="M6 11S2 7 2 4.5a4 4 0 0 1 8 0C10 7 6 11 6 11z" fill="#fff"/><circle cx="6" cy="4.5" r="1.5" fill="#a51c30"/></svg></span>
      </div>

      <div class="address">
        <p>Larkfield Court 5, 4817 Vista</p>
        <p>Orilla, Ashvale, NV</p>
      </div>
    </div>

    <svg class="footer-band" viewBox="0 0 400 120" aria-hidden="true">
      <rect width="400" height="120" fill="var(--red)"/>
      <path d="M140 -1h120v39c-28 0-50 10-60 32-10-22-32-32-60-32z" fill="var(--white)"/>
    </svg>
  </section>

  <section class="card card-back">
    <div class="pattern-field" role="img" aria-label="Faint repeating brand monogram pattern"></div>
    <div class="center-brand">
      <div class="center-mark"></div>
      <div class="center-text">
        <div class="center-name">THORNMERE</div>
        <div class="center-sub">REGIONAL CENTER</div>
      </div>
    </div>
  </section>
</body>
</html>
```